Realty Group Needs Classy, Contemporary Letterhead Design

We need a letterhead design for a new realty company located in NY, USA. We buy investment properties to rehabilitate and or keep in our rental portfolio.

```html
<!DOCTYPE html>
<html lang="en">
<head>
<meta charset="utf-8">
<title>Meridian Realty Group Letterhead</title>
<link rel="stylesheet" href="https://fonts.googleapis.com/css2?family=Lato:wght@400;700;900&family=Open+Sans:wght@400&display=swap">
<style>
  :root {
    --brand: #4e2a8e;
    --ink: #3f3f3f;
    --paper: #ffffff;
    --on-brand: #ffffff;
    --sign-tone: #ececf0;
  }
  * { margin: 0; padding: 0; box-sizing: border-box; }
  html, body { width: 1040px; height: 1200px; overflow: hidden; background: var(--paper); }
  .letterhead { position: relative; width: 1040px; height: 1200px; background: var(--paper); color: var(--ink); font-family: "Open Sans", sans-serif; }
  .brand-mark { position: absolute; right: 112px; top: 40px; text-align: center; font-family: "Lato", sans-serif; font-weight: 900; color: var(--brand); }
  .brand-name { font-size: 40px; letter-spacing: -0.5px; line-height: 1; display: flex; align-items: center; gap: 10px; }
  .brand-dot { width: 14px; height: 14px; border-radius: 50%; background: var(--brand); }
  .brand-sub { font-size: 15px; letter-spacing: 1px; margin-top: 6px; }
  .block { position: absolute; left: 98px; width: 840px; font-size: 15.5px; }
  .recipient { line-height: 18px; }
  .body-copy { line-height: 27px; text-align: justify; }
  .signature { position: absolute; left: 98px; top: 872px; width: 230px; height: 28px; }
  .signer-name { font-family: "Lato", sans-serif; font-size: 20px; color: #2f2f2f; }
  .footer-band { position: absolute; left: 0; bottom: 0; width: 100%; height: 96px; }
  .contact { position: absolute; font-family: "Lato", sans-serif; font-size: 17.5px; color: var(--on-brand); line-height: 22.5px; }
  .contact-list { left: 106px; top: 1118px; }
  .contact-list li { list-style: none; display: flex; align-items: center; gap: 7px; }
  .contact-list svg { width: 15px; height: 15px; fill: var(--on-brand); }
  .divider { position: absolute; left: 356px; top: 1122px; width: 1px; height: 64px; background: rgba(255,255,255,.5); }
  .address { left: 383px; top: 1118px; }
  .illustration { position: absolute; right: 0; bottom: 0; }
</style>
</head>
<body>
<main class="letterhead">
  <header class="brand-mark">
    <div class="brand-name"><span class="brand-dot"></span>MERIDIAN</div>
    <div class="brand-sub">Realty Group, LLC</div>
  </header>

  <p class="block" style="top:235px">Issuing Date: May 5, 2018</p>
  <address class="block recipient" style="top:272px;font-style:normal">
    Name Of Employee Mr. XYZABC<br>Address of Employee<br>Address Line 2 etc..
  </address>
  <p class="block" style="top:376px">Dear Mr.XYZABC</p>

  <p class="block body-copy" style="top:426px">Lorem Ipsum has been the industry's standard dummy text ever since the 1500s, when an unknown printer took a galley of type and scrambled it to make a type specimen book. It has survived not only five centuries, but also the leap into electronic typesetting, remaining essentially unchanged. It was popularised in the 1960s with the release of Kalvex sheets containing Lorem Ipsum passages, and more recently with desktop publishing software like Pagevane Studio including versions of Lorem Ipsum.</p>
  <p class="block body-copy" style="top:587px">Lorem Ipsum is simply dummy text of the printing and typesetting industry. Lorem Ipsum has been the industry's standard dummy text ever since the 1500s, when an unknown printer took a galley of type and scrambled it to make a type specimen book.</p>
  <p class="block body-copy" style="top:695px">It has survived not only five centuries, but also the leap into electronic typesetting, remaining essentially unchanged. It was popularised in the 1960s with the release of Kalvex sheets containing Lorem IpsumIpsum passages.</p>

  <p class="block" style="top:832px">Yours Sincerely</p>
  <div class="signature" role="img" aria-label="Handwritten signature of Daniel Hartley" style="background:var(--sign-tone)"></div>
  <p class="block signer-name" style="top:910px">Daniel Hartley</p>
  <p class="block" style="top:941px">Managing Director</p>

  <svg class="footer-band" viewBox="0 0 1040 96" preserveAspectRatio="none" aria-hidden="true">
    <polygon points="0,0 553,0 530,96 0,96" fill="var(--brand)"/>
  </svg>
  <svg class="illustration" width="500" height="276" viewBox="0 0 500 276" role="img" aria-label="Illustration of a long-haired archer drawing a bow, in brand purple">
    <defs>
      <linearGradient id="archerTone" x1="0" y1="1" x2="1" y2="0">
        <stop offset="0" stop-color="#4e2a8e"/>
        <stop offset="1" stop-color="#7a5bb5"/>
      </linearGradient>
    </defs>
    <path d="M40 276 C40 230 70 190 130 180 C190 160 230 80 300 90 C360 80 420 30 470 0 L500 0 L500 276 Z" fill="url(#archerTone)"/>
  </svg>

  <ul class="contact contact-list">
    <li><svg viewBox="0 0 16 16"><path d="M3 1h3l1 4-2 1a9 9 0 0 0 5 5l1-2 4 1v3a2 2 0 0 1-2 2A13 13 0 0 1 1 3a2 2 0 0 1 2-2z"/></svg>212-555 0148</li>
    <li><svg viewBox="0 0 16 16"><path d="M1 3h14v10H1z M1 3l7 6 7-6" fill="none" stroke="#fff" stroke-width="1.6"/></svg>hello@meridianrealty.com</li>
    <li><svg viewBox="0 0 16 16"><circle cx="8" cy="8" r="7"/><path d="M5 4c2 1 1 3 3 3s1 3 3 3M4 11l2-1" stroke="#4e2a8e" stroke-width="1.4" fill="none"/></svg>www.meridianrealty.com</li>
  </ul>
  <span class="divider"></span>
  <address class="contact address" style="font-style:normal">88, Harbor Street<br>Brooklyn New York<br>NY, 11201</address>
</main>
</body>
</html>
```